Graphic background for 10 Pull Up Banners

To produce a graphic background for a 100 cm wide by 200 cm high Pull-Up Display banner containing a Buddhist text in three languages: Tibetan, Mandarin and English. Please refer to uploaded file "Elements of Pull Up Banner". The design should be simple (not drawing attention away from the text). This design should then be varied for or extended to the next banner and so on until the 10th banner. When the banners are lined up, they should form a single design that is 1000 cm wide by 200 cm high.
An alternative way to look at the project is to produce a graphic background of 1000 cm width by 200 cm height that is then splitted into ten separate 100 cm wide by 200 cm high graphic to be used as background for 10 Buddhist texts (text 1, 2, 3, 4, 5, 6, 7, 8, 9a, 9b) on 10 Pull-Up Display Banners, the text in each banner being in the three languages mentioned earlier.
In either perspective, the design should be simple and not draw attention away from the texts. See uploaded PDF file "Examples.pdf"
Target Market(s)
For attendees at a Buddhist Event.
Look and feel
Each slider illustrates characteristics of the customer's brand and the style your logo design should communicate.

```html
<!DOCTYPE html>
<html lang="en">
<head>
<meta charset="utf-8">
<title>Pull-Up Banner Series – Dharma Texts</title>
<link rel="stylesheet" href="https://fonts.googleapis.com/css2?family=Noto+Sans+SC:wght@400;700&family=Noto+Serif+Tibetan:wght@400;700&family=Open+Sans:wght@400;600;700&display=swap">
<style>
  :root{
    --light-ink:#ffffff;
    --dark-ink:#1b1b1b;
    --ring:#e98a2c;
    --emblem-fill:#ffffff;
    --emblem-ink:#b3262d;
    --teal-a:#2a9a5c; --teal-b:#24a9a6; --teal-c:#176f88;
    --violet-a:#6b2a8c; --violet-b:#c02a92; --violet-c:#e25aa8;
    --lime-a:#3f8e3a; --lime-b:#d3e9a2; --lime-c:#1c6663;
    --amber-a:#e0571a; --amber-b:#f7ac3c; --amber-c:#3f2412;
  }
  *{box-sizing:border-box;margin:0;padding:0}
  html,body{width:1200px;height:590px;overflow:hidden;background:#fff}
  .banner-row{position:relative;width:1200px;height:590px}
  .banner{position:absolute;top:0;height:590px;width:296px;overflow:hidden;text-align:center;font-family:"Open Sans",sans-serif}
  .banner--errors{left:0;color:var(--light-ink);
    background:radial-gradient(ellipse 60% 45% at 50% 30%,rgba(200,255,240,.45),transparent 70%),
      linear-gradient(90deg,var(--teal-a),var(--teal-b) 55%,var(--teal-c))}
  .banner--desire{left:302px;width:295px;color:var(--light-ink);
    background:radial-gradient(ellipse 55% 45% at 50% 35%,rgba(255,200,240,.5),transparent 70%),
      linear-gradient(90deg,var(--violet-a),var(--violet-b) 55%,var(--violet-c))}
  .banner--signs{left:604px;width:294px;color:var(--dark-ink);
    background:radial-gradient(ellipse 55% 50% at 50% 35%,rgba(245,255,215,.9),transparent 72%),
      linear-gradient(90deg,var(--lime-a),var(--lime-b) 50%,var(--lime-c))}
  .banner--guru{left:904px;color:var(--dark-ink);
    background:radial-gradient(ellipse 55% 50% at 45% 35%,rgba(255,214,120,.85),transparent 72%),
      linear-gradient(90deg,var(--amber-a),var(--amber-b) 50%,#c85a16 85%,var(--amber-c))}

  .emblem{position:absolute;left:50%;top:6px;width:58px;height:58px;margin-left:-29px;border-radius:50%;
    background:var(--emblem-fill);border:2px solid var(--ring);display:flex;align-items:center;justify-content:center;
    font-family:"Open Sans",sans-serif;font-weight:700;font-size:9px;line-height:1.1;color:var(--emblem-ink)}
  .title{position:absolute;left:0;right:0;top:64px;font-size:10px;font-weight:600}
  .title .zh{font-family:"Noto Sans SC",sans-serif;margin-right:10px}
  .rule{position:absolute;left:16%;right:16%;height:1px;background:currentColor;opacity:.8}
  .divider{position:absolute;left:16%;right:16%;height:10px}
  .divider svg{width:100%;height:10px;display:block}

  .tibetan{position:absolute;left:0;right:0;font-family:"Noto Serif Tibetan",serif;white-space:nowrap}
  .chinese{position:absolute;left:0;right:0;font-family:"Noto Sans SC",sans-serif}
  .english{position:absolute;left:0;right:0}
  .note{position:absolute;left:0;right:0;font-family:"Noto Sans SC",sans-serif;font-size:5.5px;opacity:.9}
  .flourish{position:absolute;left:0;right:0;bottom:0}
</style>
</head>
<body>
<main class="banner-row">

  <!-- Banner 1 -->
  <section class="banner banner--errors">
    <div class="emblem">Lotus<br>Hall</div>
    <h2 class="title"><span class="zh">十个误解</span>-&nbsp;&nbsp;Ten Mistaking</h2>
    <div class="rule" style="top:85px"></div>
    <div class="tibetan" style="top:94px;font-size:7.5px;line-height:10.2px">
      དད་པ་དང་འདོད་ཆགས་ནོར་དུ་འོང་།<br>
      བྱམས་སྙིང་རྗེ་དང་ཞེན་ཆགས་ནོར་དུ་འོང་།<br>
      ཤེས་བྱ་སྟོང་པ་དང་བློས་བྱས་སྟོང་ཉིད་ནོར་དུ་འོང་།<br>
      ཆོས་དབྱིངས་དང་ཆད་ལྟ་ནོར་དུ་འོང་།<br>
      ཉམས་དང་རྟོགས་པ་ནོར་དུ་འོང་།<br>
      བཙུན་པ་དང་ལྷ་འབབས་ནོར་དུ་འོང་།<br>
      འཁྲུལ་ཞིག་དང་བདུད་ཞུགས་ནོར་དུ་འོང་།<br>
      གྲུབ་ཐོབ་དང་གཡོ་མཁན་ནོར་དུ་འོང་།<br>
      གཞན་ཕན་དང་རང་དོན་ནོར་དུ་འོང་།<br>
      ཐབས་མཁས་དང་གཡོ་སྒྱུ་ནོར་དུ་འོང་།
    </div>
    <div class="divider" style="top:200px"><svg viewBox="0 0 200 10" preserveAspectRatio="none"><line x1="0" y1="5" x2="200" y2="5" stroke="currentColor" stroke-width=".6"/><path d="M94 5 L100 1 L106 5 L100 9Z" fill="currentColor"/></svg></div>
    <p class="chinese" style="top:228px;font-size:8.6px;line-height:13.6px">
      信心与爱欲可能混淆，<br>慈悲与贪执可能混淆，<br>所知¹本空与思维造作空性可能混淆，<br>法界与断见²可能混淆，<br>觉受与证悟可能混淆，<br>尊者与神棍可能混淆，<br>破惑与着魔可能混淆，<br>成就者与骗子可能混淆，<br>利他与自利可能混淆，<br>方便善巧与谄媚哄骗可能混淆。
    </p>
    <p class="note" style="top:370px;line-height:8px">1、所知：可以认识的外境。<br>2、断灭：否定因果、前生、后世等说法的见解。</p>
    <div class="divider" style="top:398px"><svg viewBox="0 0 200 10" preserveAspectRatio="none"><line x1="0" y1="5" x2="200" y2="5" stroke="currentColor" stroke-width=".6"/><path d="M94 5 L100 1 L106 5 L100 9Z" fill="currentColor"/></svg></div>
    <p class="english" style="top:418px;font-size:5.8px;line-height:11px;font-weight:600">
      Desire can be mistaken for faith or devotion.<br>
      Attachment can be mistaken for love and compassion.<br>
      Conceptual emptiness can be mistaken for the emptiness of the nature of phenomena.<br>
      Nihilism can be mistaken for the dharmadhatu.<br>
      A meditative experience can be mistaken for realization.<br>
      Outer religious practices can be mistaken for inner development of good qualities.<br>
      A person in the grip of a demon can be mistaken for a person who has destroyed his own delusions.<br>
      A charlatan can be mistaken for a siddha.<br>
      An act to benefit yourself can be mistaken for an act to benefit others.<br>
      Deviousness can be mistaken for skilful means.
    </p>
    <div class="flourish" role="img" aria-label="White floral flourish rising from the bottom edge" style="height:60px;background:linear-gradient(to top,rgba(255,255,255,.55),rgba(255,255,255,0))"></div>
  </section>

  <!-- Banner 2 -->
  <section class="banner banner--desire">
    <div class="emblem">Lotus<br>Hall</div>
    <h2 class="title" style="font-weight:400"><span class="zh">欲与爱</span>-&nbsp;&nbsp;Desire &amp; Attachment</h2>
    <div class="rule" style="top:85px"></div>
    <div class="tibetan" style="top:102px;font-size:10.5px;line-height:19px">
      འདོད་པ་མེད་ན་རང་དོན་མི་འགྲུབ་ཀྱང་།<br>
      འདོད་པ་ཡོད་ཚད་ཆགས་པ་མ་ཡིན་པས།<br>
      འདོད་དང་ཆགས་པའི་ཁྱད་པར་མ་ཤེས་པར།<br>
      འདོད་ཆགས་ལམ་དུ་སློང་བ་ལབ་པ་རེ།
    </div>
    <div class="divider" style="top:200px"><svg viewBox="0 0 200 10" preserveAspectRatio="none"><line x1="0" y1="5" x2="200" y2="5" stroke="currentColor" stroke-width=".6"/><path d="M94 5 L100 1 L106 5 L100 9Z" fill="currentColor"/></svg></div>
    <p class="chinese" style="top:226px;font-size:13px;line-height:20px">
      若无意欲则不成自利，<br>然有意欲非为执着故，<br>不知意欲执着差别即，<br>贪执说所当取确荒唐。
    </p>
    <div class="divider" style="top:320px"><svg viewBox="0 0 200 10" preserveAspectRatio="none"><line x1="0" y1="5" x2="200" y2="5" stroke="currentColor" stroke-width=".6"/><path d="M94 5 L100 1 L106 5 L100 9Z" fill="currentColor"/></svg></div>
    <p class="english" style="top:344px;font-size:8px;line-height:19px;font-weight:600">
      If you have no desire, your goal cannot be achieved.<br>
      Since not all desire is attachment,<br>
      not knowing how to differentiate desire from attachment,<br>
      to talk about bringing passion into the path is absurd.
    </p>
    <div class="flourish" role="img" aria-label="White floral swirls across the lower part of the banner" style="height:140px;background:linear-gradient(to top,rgba(255,255,255,.45),rgba(255,255,255,0))"></div>
  </section>

  <!-- Banner 3 -->
  <section class="banner banner--signs">
    <div class="flourish" role="img" aria-label="Small white floral corner flourish" style="top:0;bottom:auto;height:40px;width:60px;background:radial-gradient(circle at 0 0,rgba(255,255,255,.45),transparent 70%)"></div>
    <div class="emblem">Lotus<br>Hall</div>
    <h2 class="title" style="font-weight:400;font-size:8.4px"><span class="zh">曾修过佛法的相状</span>-&nbsp;&nbsp;Signs Of Having Practised The Dharma</h2>
    <div class="rule" style="top:85px"></div>
    <div class="tibetan" style="top:97px;font-size:9.6px;line-height:18px">
      རང་ལུས་ཡོངས་སུ་བཏང་ནས་བསྒྲུབས་ཤེས་ན།<br>
      དལ་འབྱོར་སྙིང་པོ་བླངས་པ་ཡིན་པའི་རྟགས།<br>
      གསེར་དང་རྡོ་བ་མཉམ་པར་མཐོང་ཤེས་ན།<br>
      མི་རྟག་སྒྱུ་མ་རྒྱུད་ལ་སྐྱེས་པའི་རྟགས།<br>
      འཁོར་བའི་ཆོས་ལ་དགྲ་རུ་མཐོང་ཤེས་ན།<br>
      སྡུག་བསྔལ་རྒྱ་མཚོའི་ཕ་རོལ་འགྲོ་བའི་རྟགས།
    </div>
    <div class="divider" style="top:222px"><svg viewBox="0 0 200 10" preserveAspectRatio="none"><line x1="0" y1="5" x2="200" y2="5" stroke="currentColor" stroke-width=".6"/><path d="M94 5 L100 1 L106 5 L100 9Z" fill="currentColor"/></svg></div>
    <div class="chinese" style="top:240px;font-size:9.8px;line-height:13.5px;font-weight:700;text-align:left;left:68px;right:20px">
      <p>若懂舍自身富而修行，<br>表示取得真贵暇满¹义；</p>
      <p style="margin-top:13px">若懂金与土块平等观，<br>表示‘无常’‘如幻’心中生；</p>
      <p style="margin-top:13px">若视轮回现象为敌人，<br>表示渡往苦海之彼岸。</p>
      <p style="margin-top:5px;font-size:5.5px;font-weight:400;line-height:8px">1、暇满：八有暇和十圆满。</p>
    </div>
    <div class="divider" style="top:358px"><svg viewBox="0 0 200 10" preserveAspectRatio="none"><line x1="0" y1="5" x2="200" y2="5" stroke="currentColor" stroke-width=".6"/><path d="M94 5 L100 1 L106 5 L100 9Z" fill="currentColor"/></svg></div>
    <div class="english" style="top:374px;font-size:5.8px;line-height:8.4px;font-weight:600">
      <p>If you know not to cherish your body but use it to attain<br>accomplishments (in the Dharma),<br>it is a sign that you have gotten the essence<br>of your precious freedoms and fortunes.</p>
      <p style="margin-top:8px">If you know the sameness of gold and dirt<br>while in meditative equipoise, it is a sign that<br>the insight of impermanence and illusion have arisen in your mental continuum.</p>
      <p style="margin-top:8px">If you know to see samsaric phenomena as an enemy,<br>it is a sign that you are heading to the other shore<br>of the ocean of suffering.</p>
      <p style="margin-top:8px">1. Freedom and fortunes: the eight freedoms and ten fortunes</p>
    </div>
    <div class="flourish" role="img" aria-label="White floral flourish in the lower right corner" style="left:auto;width:120px;height:70px;background:radial-gradient(circle at 70% 100%,rgba(255,255,255,.5),transparent 70%)"></div>
  </section>

  <!-- Banner 4 -->
  <section class="banner banner--guru">
    <div class="emblem">Lotus<br>Hall</div>
    <h2 class="title" style="font-weight:400;font-size:8.6px"><span class="zh">上师之恩德</span>-&nbsp;&nbsp;Kindness Of The Guru</h2>
    <div class="rule" style="top:85px"></div>
    <div class="tibetan" style="top:97px;font-size:11px;line-height:20.5px">
      བླ་མ་བརྗེད་དུ་མ་སྲིད།<br>
      སངས་རྒྱས་མང་པོ་བྱོན་གྱུར་ཀྱང་།<br>
      བདག་ནི་སུ་ཡིས་རྗེས་མ་བཟུང་།<br>
      ཁྱེད་ཀྱིས་མ་དོར་ཐུགས་རྗེས་བསྐྱངས།<br>
      སངས་རྒྱས་སྟོང་ལས་ཁྱེད་དྲིན་ཆེ།
    </div>
    <div class="divider" style="top:218px"><svg viewBox="0 0 200 10" preserveAspectRatio="none"><line x1="0" y1="5" x2="200" y2="5" stroke="currentColor" stroke-width=".6"/><path d="M94 5 L100 1 L106 5 L100 9Z" fill="currentColor"/></svg></div>
    <p class="chinese" style="top:240px;font-size:12px;line-height:21px">
      切莫忘记上师。<br>即使众多佛降临，<br>谁皆未曾摄受我，<br>您不舍弃悲悯护，<br>您比千佛恩更大。
    </p>
    <div class="divider" style="top:352px"><svg viewBox="0 0 200 10" preserveAspectRatio="none"><line x1="0" y1="5" x2="200" y2="5" stroke="currentColor" stroke-width=".6"/><path d="M94 5 L100 1 L106 5 L100 9Z" fill="currentColor"/></svg></div>
    <p class="english" style="top:370px;font-size:8.6px;line-height:14px">
      Do not forget the guru.<br>
      Although many Buddhas had appeared,<br>
      <span style="display:block;margin-top:5px">none has taken hold of me.</span>
      <span style="display:block;margin-top:5px">You did not abandon me, but lovingly and</span>
      <span style="display:block;margin-top:5px">compassionately protected me.</span>
    </p>
    <p class="english" style="top:507px;font-size:8.6px">Your kindness is greater than a thousand Buddhas'.</p>
    <div class="flourish" role="img" aria-label="White floral flourish along the bottom edge" style="height:50px;background:linear-gradient(to top,rgba(255,255,255,.5),rgba(255,255,255,0))"></div>
  </section>

</main>
</body>
</html>
```